Venture Capital Firm Needs Website Redesign

We need a bold revamp of our website (https://halverine.vc/)
which at the moment looks washed out. We want a crisp, fresh and unique look. Feel free to keep as much or as little content in the site. The only thing we need to keep is a team section. The site should convey a clear distinction between our 3 product lines: Venture Capital, Private Credit, and Crypto. Two versions of our logo are attached and they should not change. For design inspirations, we like http://www.9plm.com/ for a more simple site and for a more built out site we like http://bluetorch.com/

Updates
Industry/Entity Type
Investment
Coding
Coded - Design and coding required
Number of Pages Required
1 page
Font styles to use
Colors
Designer to choose colors to be used in the design.
Requirements
Must have
- - Clear distinction between our 3 product lines: Venture Capital, Private Credit
- - Team section

Nice to have
- Some really creative aspect like http://www.9plm.com/ has with the distinction between first, second, and third kind

```html
<!DOCTYPE html>
<html lang="en">
<head>
<meta charset="utf-8">
<title>Halverine</title>
<link href="https://fonts.googleapis.com/css2?family=Montserrat:wght@400;500;600;700&family=Questrial&display=swap" rel="stylesheet">
<style>
:root{
  --navy:#2f3189;
  --navy-tile:#3a3d95;
  --blue:#1d3cc4;
  --periwinkle:#93a2ee;
  --green:#8ea63a;
  --lime:#c9d43c;
  --ink:#2a2c6e;
  --text:#5c5f73;
  --muted:#b9bccb;
  --line:#e3e4ea;
  --dark:#3a3a3c;
  --white:#ffffff;
}
*{margin:0;padding:0;box-sizing:border-box}
html,body{width:1200px;height:3364px;overflow:hidden}
body{font-family:"Questrial",sans-serif;color:var(--text);background:var(--white)}
.section-title{font-family:"Montserrat",sans-serif;font-weight:600;font-size:26px;letter-spacing:1px;text-transform:uppercase}
.section-mark{font-family:"Montserrat",sans-serif;font-weight:400;font-size:40px;letter-spacing:3px;text-transform:uppercase;margin-top:6px}
p.copy{font-size:15px;line-height:1.75}

/* hero */
.hero{height:620px;position:relative;overflow:hidden;background:linear-gradient(100deg,var(--blue) 0%,#3a4eb2 38%,#6f8f55 72%,var(--green) 100%)}
.hero .bubble{position:absolute;border-radius:50%}
.bubble.b1{width:330px;height:330px;left:175px;top:125px;background:rgba(214,150,210,.55)}
.bubble.b2{width:220px;height:220px;left:110px;top:420px;background:rgba(170,190,120,.45)}
.bubble.b3{width:260px;height:260px;left:560px;top:360px;background:rgba(190,120,200,.35)}
.bubble.b4{width:300px;height:300px;left:820px;top:-40px;background:rgba(120,170,90,.35)}
.bubble.b5{width:180px;height:180px;left:990px;top:420px;background:rgba(200,150,200,.3)}
.topbar{position:relative;display:flex;align-items:center;justify-content:space-between;padding:36px 150px 0 160px}
.brand{font-family:"Montserrat",sans-serif;font-weight:600;font-size:30px;letter-spacing:2px;color:var(--lime)}
.nav{display:flex;gap:40px;list-style:none}
.nav a{font-family:"Montserrat",sans-serif;font-size:12px;font-weight:600;color:var(--white);text-decoration:none;letter-spacing:1px;text-transform:uppercase;opacity:.85}
.nav a.active{opacity:1;border-bottom:2px solid var(--white);padding-bottom:4px}
.hero h1{position:relative;font-family:"Montserrat",sans-serif;font-weight:700;font-size:36px;line-height:1.45;color:var(--white);text-align:center;width:860px;margin:170px auto 0}

/* venture capital */
.venture{height:700px;background:var(--navy);padding:90px 160px 0;position:relative}
.split{display:flex;justify-content:space-between}
.venture .section-title{color:var(--white);font-weight:500}
.venture .section-mark{color:#55589f}
.venture p.copy{width:470px;color:#aeb1d8}
.portfolio{display:flex;gap:24px;justify-content:center;margin-top:120px}
.portfolio .tile{width:190px;height:150px;background:var(--navy-tile);display:flex;align-items:center;justify-content:center;gap:10px;color:var(--white);font-family:"Montserrat",sans-serif;font-weight:500;font-size:22px}
.tile .dot{width:14px;height:14px;background:var(--white)}

/* private credit */
.credit{height:620px;background:var(--white);border-top-left-radius:320px 110px;margin-top:-110px;position:relative;padding:130px 160px 0}
.credit .section-title{color:var(--ink)}
.credit .section-mark{color:#dfe1a8}
.credit p.copy{width:560px}
.credit hr{border:0;border-top:1px solid var(--line);margin:40px 0 50px}
.partners{display:flex;gap:40px}
.ring{position:relative;width:180px;height:180px;border:3px solid var(--dark);border-radius:50%;display:flex;align-items:center;justify-content:center;text-align:center;font-family:"Montserrat",sans-serif;font-weight:600;font-size:16px;color:var(--ink)}
.ring .knob{position:absolute;width:14px;height:14px;border-radius:50%;background:var(--dark)}
.knob.n{top:-8px;left:50%;margin-left:-7px}
.knob.s{bottom:-8px;left:50%;margin-left:-7px}
.knob.w{left:-8px;top:50%;margin-top:-7px}
.knob.e{right:-8px;top:50%;margin-top:-7px}
.ring .badge{width:22px;height:22px;border-radius:50%;background:var(--green);margin-right:8px;flex:none}

/* crypto */
.crypto{height:720px;padding:110px 30px 0 150px}
.crypto-card{height:480px;border-radius:14px;background:linear-gradient(100deg,var(--periwinkle) 0%,#5f74e0 45%,var(--blue) 100%);display:flex;padding:60px 50px;gap:60px;box-shadow:0 12px 30px rgba(40,60,160,.18)}
.crypto-copy{width:400px}
.crypto .section-title{color:var(--white)}
.crypto .section-mark{color:#b7c2f5}
.crypto p.copy{color:#eef0ff;margin-top:24px}
.btn{display:inline-block;margin-top:34px;padding:12px 26px;border:1px solid var(--white);border-radius:4px;color:var(--white);font-size:13px;font-family:"Montserrat",sans-serif;text-decoration:none}
.chart{flex:1}

/* team */
.team{height:540px;display:flex;justify-content:center;gap:110px;padding-top:40px}
.member{width:290px;text-align:center}
.member .ring{width:240px;height:240px;margin:0 auto}
.portrait{width:222px;height:222px;border-radius:50%;background:radial-gradient(circle at 50% 40%,#cfcfcf,#6e6e6e)}
.member h3{font-family:"Montserrat",sans-serif;font-size:17px;font-weight:600;color:var(--ink);margin-top:36px}
.member p{font-size:14px;line-height:1.6;margin-top:16px;color:var(--text)}

/* footer */
.footer{height:110px;background:var(--green);display:flex;align-items:center;justify-content:space-between;padding:0 150px 0 160px;color:var(--white);font-size:14px}
.contact{display:flex;gap:34px;align-items:center}
.contact span{display:flex;align-items:center;gap:8px}
.footer .nav a{font-size:13px;opacity:1;text-transform:none;letter-spacing:0}
.legal{height:54px;background:var(--dark);color:#c7c7c7;font-size:12px;display:flex;align-items:center;justify-content:center}
</style>
</head>
<body>

<header class="hero">
  <span class="bubble b1"></span><span class="bubble b2"></span><span class="bubble b3"></span><span class="bubble b4"></span><span class="bubble b5"></span>
  <div class="topbar">
    <div class="brand">HALVERINE</div>
    <ul class="nav">
      <li><a class="active" href="#venture">Venture</a></li>
      <li><a href="#credit">Private Credit</a></li>
      <li><a href="#crypto">Crypto</a></li>
      <li><a href="#about">About Us</a></li>
      <li><a href="#team">Team</a></li>
      <li><a href="#blog">Blog</a></li>
    </ul>
  </div>
  <h1>Halverine operates at the intersection of technology and novel asset classes.</h1>
</header>

<section class="venture" id="venture">
  <div class="split">
    <div>
      <div class="section-title">Venture Capital</div>
      <div class="section-mark">Halverine</div>
    </div>
    <p class="copy">We invest in early stage startups led by founders who are passionate and knowledgeable about the markets they serve. We have our own software developers and product managers. We work with the founders in our portfolio to help them bring products to market, sourcing equity for the work and for the cash we invest in their companies.</p>
  </div>
  <div class="portfolio">
    <div class="tile"><span class="dot"></span>Vellcode</div>
    <div class="tile">Tinyroam</div>
    <div class="tile">ExecLoom</div>
    <div class="tile">Marlo Capital</div>
  </div>
</section>

<section class="credit" id="credit">
  <div class="split">
    <div>
      <div class="section-title">Private Credit</div>
      <div class="section-mark">Halverine</div>
    </div>
    <p class="copy">Halverine Private Credit provides capital to lending businesses that are focused on using technology to establish new credit markets, create new credit products or dramatically re-invent an existing form of credit. We believe that the pioneers who build something truly different in a credit market will create the most lucrative business models. Given our heritage as a venture firm, we are comfortable with emerging businesses and can provide capital for a company's first loan.</p>
  </div>
  <hr>
  <div class="partners">
    <div class="ring"><span class="knob n"></span><span class="knob s"></span><span class="knob w"></span><span class="knob e"></span><span class="badge"></span>Seedwell</div>
    <div class="ring"><span class="knob n"></span><span class="knob s"></span><span class="knob w"></span><span class="knob e"></span>Fenmora<br>Financial</div>
    <div class="ring"><span class="knob n"></span><span class="knob s"></span><span class="knob w"></span><span class="knob e"></span>Brightledger</div>
  </div>
</section>

<section class="crypto" id="crypto">
  <div class="crypto-card">
    <div class="crypto-copy">
      <div class="section-title">Crypto</div>
      <div class="section-mark">Halverine</div>
      <p class="copy">The Halverine Crypto Index tracks the top 10 cryptocurrencies weighted by market cap and rebalanced twice a month. We believe this is the simplest and most cost-effective way to obtain cryptocurrency exposure. Our process has been designed by experts from financial services and cryptocurrency industries.</p>
      <a class="btn" href="#crypto">Learn More</a>
    </div>
    <svg class="chart" viewBox="0 0 460 360" role="img" aria-label="Line chart of index cumulative growth against a benchmark">
      <text x="230" y="16" text-anchor="middle" font-family="Montserrat, sans-serif" font-size="11" fill="#ffffff">Index Cumulative Growth</text>
      <circle cx="140" cy="36" r="5" fill="#e6e13a"/><text x="150" y="40" font-size="10" fill="#ffffff" font-family="Questrial, sans-serif">Index (TOP 10)</text>
      <circle cx="260" cy="36" r="5" fill="#111111"/><text x="270" y="40" font-size="10" fill="#ffffff" font-family="Questrial, sans-serif">Benchmark (BTC)</text>
      <g stroke="rgba(255,255,255,.25)" stroke-width="1">
        <line x1="40" y1="70" x2="450" y2="70"/><line x1="40" y1="115" x2="450" y2="115"/><line x1="40" y1="160" x2="450" y2="160"/>
        <line x1="40" y1="205" x2="450" y2="205"/><line x1="40" y1="250" x2="450" y2="250"/><line x1="40" y1="295" x2="450" y2="295"/>
      </g>
      <line x1="40" y1="320" x2="450" y2="320" stroke="#ffffff" stroke-width="1"/>
      <g font-size="10" fill="#ffffff" font-family="Questrial, sans-serif" text-anchor="end">
        <text x="34" y="74">3500</text><text x="34" y="119">3000</text><text x="34" y="164">2500</text>
        <text x="34" y="209">2000</text><text x="34" y="254">1500</text><text x="34" y="299">1000</text><text x="34" y="324">500</text>
      </g>
      <g font-size="9" fill="#ffffff" font-family="Questrial, sans-serif" text-anchor="middle">
        <text x="55" y="338">Jan</text><text x="90" y="338">Feb</text><text x="125" y="338">Mar</text><text x="160" y="338">Apr</text>
        <text x="195" y="338">May</text><text x="230" y="338">Jun</text><text x="265" y="338">Jul</text><text x="300" y="338">Aug</text>
        <text x="335" y="338">Sep</text><text x="370" y="338">Oct</text><text x="405" y="338">Nov</text><text x="440" y="338">Dec</text>
      </g>
      <polyline fill="none" stroke="#e6e13a" stroke-width="2.5" points="45,318 80,316 115,314 150,311 185,307 220,300 250,290 280,272 305,250 330,215 350,170 370,110 385,80 400,120 415,170 430,205 445,230"/>
      <polyline fill="none" stroke="#111111" stroke-width="2.5" points="45,319 80,318 115,317 150,316 185,314 220,311 250,307 280,298 305,285 330,265 350,240 370,200 385,170 400,215 415,245 430,262 445,272"/>
    </svg>
  </div>
</section>

<section class="team" id="team">
  <div class="member">
    <div class="ring"><span class="knob n"></span><span class="knob s"></span><span class="knob w"></span><span class="knob e"></span><div class="portrait" role="img" aria-label="Black and white portrait of Omar Reyes"></div></div>
    <h3>Omar Reyes</h3>
    <p>He is a Partner for Halverine VC Fund. He is also a co-founder of Halverine.</p>
  </div>
  <div class="member">
    <div class="ring"><span class="knob n"></span><span class="knob s"></span><span class="knob w"></span><span class="knob e"></span><div class="portrait" role="img" aria-label="Black and white portrait of Tarun Mehlani"></div></div>
    <h3>Tarun Mehlani</h3>
    <p>He is a Partner for Halverine Crypto. He previously invested at Brightmoor Capital and Hart.</p>
  </div>
  <div class="member">
    <div class="ring"><span class="knob n"></span><span class="knob s"></span><span class="knob w"></span><span class="knob e"></span><div class="portrait" role="img" aria-label="Black and white portrait of Samir Kadeer"></div></div>
    <h3>Samir Kadeer</h3>
    <p>He is a Partner for Halverine VC Fund. He is also a co-founder of Halverine and Vellcode.</p>
  </div>
</section>

<footer class="footer">
  <div class="contact">
    <span><svg width="14" height="18" viewBox="0 0 14 18"><path d="M7 0C3.1 0 0 3.1 0 7c0 5 7 11 7 11s7-6 7-11c0-3.9-3.1-7-7-7zm0 9.5A2.5 2.5 0 1 1 7 4.5a2.5 2.5 0 0 1 0 5z" fill="#ffffff"/></svg>418 Larkin Avenue, Suite 900, New York, NY 10012</span>
    <span><svg width="18" height="13" viewBox="0 0 18 13"><rect x="0.5" y="0.5" width="17" height="12" fill="none" stroke="#ffffff"/><path d="M1 1l8 6 8-6" fill="none" stroke="#ffffff"/></svg>hello@halverine.vc</span>
  </div>
  <ul class="nav">
    <li><a href="#venture">Venture</a></li>
    <li><a href="#credit">Private Credit</a></li>
    <li><a href="#crypto">Crypto</a></li>
    <li><a href="#about">About Us</a></li>
    <li><a href="#team">Team</a></li>
    <li><a href="#blog">Blog</a></li>
  </ul>
</footer>
<div class="legal">Copyright © 2018, Halverine. All Rights Reserved.</div>

</body>
</html>
```